4th Generation Family Business Needs a New Card Design!

We are a family owned 4th Generation company. We are based in the Sydney, Australia area and we are desperately in need of a more modern and classy card. We are monumental masons who design, supply & erect lasting memorials throughout cemeteries in Sydney. Our customers are normally in a period of grieving. I have attached logo files that will need to be implemented on the card. Company was established 1935. Australian Owned and Operated. Card needs to be designed to PIXO.com specification.

Target Market(s)

Our target market is based upon people that a grieving for family members that have passed away. We also deal with alot of companies that own and operate cemeteries.

Industry/Entity Type

Business

Contact Information for Business Card

Simon Harcourt, Operations Manager, 0417293086, simon@harcourtmemorials.com.au
Lewis Harcourt, Director, 0491630572, lewis@harcourtmemorials.com.au
Phone # 02 9561 3048
Website: www.harcourtmemorials.com.au
Address: Suite 17, 8 Palfrey Lane, West Carlow, Sydney NSW 2156

Font styles to use
Serif
Decorative
Script

Requirements
Must have
• Would like to see the logo nicely implemented with a modern design. Embossed lettering would be a nice additive.

```html
<!DOCTYPE html>
<html lang="en">
<head>
<meta charset="utf-8">
<title>Harcourt Memorials – Business Card</title>
<link rel="stylesheet" href="https://fonts.googleapis.com/css2?family=PT+Sans:wght@400;700&display=swap">
<style>
  :root {
    --stage: #000000;
    --paper: #f4f4f4;
    --charcoal: #231f20;
    --gold: #e9bf2e;
    --white: #ffffff;
  }
  * { margin: 0; padding: 0; box-sizing: border-box; }
  html, body {
    width: 1200px; height: 900px; overflow: hidden;
    background: var(--stage);
    font-family: "PT Sans", Arial, sans-serif;
  }
  .stage { position: relative; width: 1200px; height: 900px; }
  .card {
    position: absolute; top: 200px;
    width: 310px; height: 502px;
    overflow: hidden;
  }
  .card--front { left: 265px; background: var(--paper); border-radius: 55px 0 55px 0; }
  .card--back { left: 641px; width: 309px; background: var(--gold); border-radius: 0 55px 0 55px; }
  .card__base { position: absolute; inset: 0; width: 100%; height: 100%; }
  .card__base path { fill: var(--charcoal); }

  .brand {
    position: absolute; left: 0; right: 0; top: 78px;
    display: flex; flex-direction: column; align-items: center; gap: 14px;
  }
  .brand__mark { width: 34px; height: 34px; background: var(--charcoal); }
  .brand__name {
    font-size: 27px; font-weight: 700; line-height: 1.1;
    text-align: center; letter-spacing: 1px; text-transform: uppercase;
    color: var(--charcoal);
  }
  .card--back .brand { top: 58px; }
  .card--back .brand__mark { background: var(--white); }
  .card--back .brand__name { color: var(--white); }

  .contact { position: absolute; left: 25px; color: var(--white); }
  .contact--first { top: 280px; }
  .contact--second { top: 371px; }
  .contact__name { color: var(--gold); font-size: 17px; font-weight: 700; line-height: 20px; }
  .contact__role { font-size: 13.5px; line-height: 18px; margin-bottom: 5px; }
  .contact__line {
    display: flex; align-items: center; gap: 7px;
    font-size: 13.5px; line-height: 18px; padding-left: 3px;
  }
  .icon { width: 10px; height: 10px; fill: var(--gold); flex: none; }

  .details { position: absolute; right: 30px; color: var(--white); text-align: right; }
  .details--phone { top: 341px; }
  .details--address { top: 406px; }
  .details__line {
    display: flex; justify-content: flex-end; align-items: center; gap: 10px;
    font-size: 13.5px; line-height: 19px;
  }
  .details__address { display: flex; align-items: center; gap: 10px; font-size: 13.5px; line-height: 18px; }
  .details__address .icon { width: 11px; height: 14px; }
</style>
</head>
<body>
<main class="stage">

  <section class="card card--front" aria-label="Card front">
    <svg class="card__base" viewBox="0 0 310 502" preserveAspectRatio="none" aria-hidden="true">
      <path d="M0,232 Q125,222 245,284 L245,328 L277,328 Q305,345 310,400 L310,502 L0,502 Z"/>
    </svg>
    <div class="brand">
      <span class="brand__mark"></span>
      <span class="brand__name">Harcourt<br>Memorials</span>
    </div>
    <div class="contact contact--first">
      <p class="contact__name">Simon Harcourt</p>
      <p class="contact__role">Operations Manager</p>
      <p class="contact__line"><svg class="icon" viewBox="0 0 10 10"><path d="M2,0.5 L3.6,2.6 L2.8,3.7 Q4,6 6.3,7.2 L7.4,6.4 L9.5,8 L8.4,9.5 Q4.5,9.3 0.5,1.6 Z"/></svg>0417293086</p>
      <p class="contact__line"><svg class="icon" viewBox="0 0 10 10"><path d="M0,2 H10 V8.5 H0 Z M0.8,2.6 L5,5.6 L9.2,2.6" stroke="#231f20" stroke-width="0.8"/></svg>simon@harcourtmemorials.com.au</p>
    </div>
    <div class="contact contact--second">
      <p class="contact__name">Lewis Harcourt</p>
      <p class="contact__role">Director</p>
      <p class="contact__line"><svg class="icon" viewBox="0 0 10 10"><path d="M2,0.5 L3.6,2.6 L2.8,3.7 Q4,6 6.3,7.2 L7.4,6.4 L9.5,8 L8.4,9.5 Q4.5,9.3 0.5,1.6 Z"/></svg>0491630572</p>
      <p class="contact__line"><svg class="icon" viewBox="0 0 10 10"><path d="M0,2 H10 V8.5 H0 Z M0.8,2.6 L5,5.6 L9.2,2.6" stroke="#231f20" stroke-width="0.8"/></svg>lewis@harcourtmemorials.com.au</p>
    </div>
  </section>

  <section class="card card--back" aria-label="Card back">
    <svg class="card__base" viewBox="0 0 309 502" preserveAspectRatio="none" aria-hidden="true">
      <path d="M309,250 Q190,252 62,300 L62,346 L29,346 Q4,362 0,415 L0,502 L309,502 Z"/>
    </svg>
    <div class="brand">
      <span class="brand__mark"></span>
      <span class="brand__name">Harcourt<br>Memorials</span>
    </div>
    <div class="details details--phone">
      <p class="details__line">02 9561 3048<svg class="icon" viewBox="0 0 10 10"><path d="M2,0.5 L3.6,2.6 L2.8,3.7 Q4,6 6.3,7.2 L7.4,6.4 L9.5,8 L8.4,9.5 Q4.5,9.3 0.5,1.6 Z"/></svg></p>
      <p class="details__line">www.harcourtmemorials.com.au<svg class="icon" viewBox="0 0 10 10"><circle cx="5" cy="5" r="5"/><path d="M2,3 Q4,2 5,4 Q4,6 6,7 L5,9.5 M7,1.5 L6.5,3.5 L8.5,4.5" stroke="#231f20" stroke-width="0.9" fill="none"/></svg></p>
    </div>
    <div class="details details--address">
      <div class="details__address">
        <p>Suite 17, 8 Palfrey Lane, West Carlow,<br>Sydney NSW 2156</p>
        <svg class="icon" viewBox="0 0 11 14"><path d="M5.5,0 A5.5,5.5 0 0 1 11,5.5 Q11,8.5 5.5,14 Q0,8.5 0,5.5 A5.5,5.5 0 0 1 5.5,0 Z M5.5,3.3 A2.2,2.2 0 1 0 5.5,7.7 A2.2,2.2 0 1 0 5.5,3.3 Z" fill-rule="evenodd"/></svg>
      </div>
    </div>
  </section>

</main>
</body>
</html>
```